Tech business card design

We need an amazing business card design for our new business 'Pexla' a marketing tech startup based in Sydney, Australia. We provide an online marketplace for businesses to search and buy advertising media, connect with service providers and learn more about marketing. We wish to communicate 'cool tech', reliability and professionalism and design based around our logo.

Target Market(s)

Business Owners

Contact Information for Business Card

Name
Position
Email Address
Website
Phone Number

Font styles to use
Other font styles liked:
• Avenir & Avenir Next

Colors

Designer to choose colors to be used in the design.

```html
<!DOCTYPE html>
<html lang="en">
<head>
<meta charset="utf-8">
<title>Pexla Business Card</title>
<link href="https://fonts.googleapis.com/css2?family=Nunito+Sans:wght@400;700;900&display=swap" rel="stylesheet">
<style>
  :root {
    --stage: #1c1c1f;
    --paper: #ffffff;
    --navy: #1a1f48;
    --navy-deep: #161b40;
    --ghost: #6e7299;
    --ink: #1a1a1a;
    --accent-edge: #7a1f35;
  }
  * { margin: 0; padding: 0; box-sizing: border-box; }
  html, body {
    width: 1200px; height: 803px; overflow: hidden;
    background: var(--stage);
    font-family: "Nunito Sans", Arial, sans-serif;
  }
  .card {
    position: absolute;
    width: 525px; height: 300px;
    border-radius: 4px;
    overflow: hidden;
  }
  .card-front { left: 50px; top: 250px; background: var(--paper); border-bottom: 3px solid var(--accent-edge); }
  .card-back { left: 625px; top: 250px; background: var(--navy-deep); }

  .brand-name {
    position: absolute;
    font-weight: 900;
    color: var(--navy);
    letter-spacing: -2px;
    line-height: 1;
  }
  .card-front .brand-name { right: 60px; top: 30px; font-size: 92px; }

  .name-tab {
    position: absolute; left: 0; top: 112px;
    width: 14px; height: 36px;
    background: var(--navy);
    border-radius: 0 8px 8px 0;
  }
  .holder { position: absolute; left: 26px; top: 110px; color: var(--ink); }
  .holder-name { font-size: 17px; font-weight: 900; letter-spacing: 0.3px; }
  .holder-role { font-size: 12px; font-weight: 700; margin-top: 1px; }

  .address { position: absolute; left: 26px; top: 186px; font-size: 13px; line-height: 1.3; color: var(--ink); }
  .contacts { position: absolute; left: 26px; top: 236px; list-style: none; font-size: 13px; color: var(--ink); }
  .contacts li { display: flex; align-items: center; gap: 8px; line-height: 1.6; }
  .contacts svg { width: 12px; height: 12px; fill: var(--ink); }

  .web-band {
    position: absolute; right: 0; top: 152px;
    width: 250px; height: 32px;
    background: var(--navy);
    border-radius: 16px 0 0 16px;
    color: #fff; font-size: 12px; letter-spacing: 3px;
    display: flex; align-items: center; justify-content: center;
  }

  .card-back .brand-name {
    left: 50%; top: 50%;
    transform: translate(-50%, -50%);
    font-size: 150px;
    color: var(--ghost);
  }
</style>
</head>
<body>
  <section class="card card-front" aria-label="Card front">
    <div class="brand-name">pexla</div>
    <span class="name-tab"></span>
    <div class="holder">
      <p class="holder-name">JOHN SMITH</p>
      <p class="holder-role">Position</p>
    </div>
    <p class="address">Street Name, City Name<br>Zipcode:012345</p>
    <ul class="contacts">
      <li><svg viewBox="0 0 24 24" aria-hidden="true"><path d="M6.6 10.8a15.1 15.1 0 0 0 6.6 6.6l2.2-2.2a1 1 0 0 1 1-.25 11.4 11.4 0 0 0 3.6.57 1 1 0 0 1 1 1V20a1 1 0 0 1-1 1A17 17 0 0 1 3 4a1 1 0 0 1 1-1h3.5a1 1 0 0 1 1 1c0 1.25.2 2.45.57 3.57a1 1 0 0 1-.25 1z"/></svg>012-345-6789</li>
      <li><svg viewBox="0 0 24 24" aria-hidden="true"><path d="M2 5h20v14H2zM3.5 6.5 12 13l8.5-6.5v1.8L12 14.8 3.5 8.3z" fill-rule="evenodd"/></svg>info@pexla.com</li>
    </ul>
    <div class="web-band">www.pexla.com</div>
  </section>

  <section class="card card-back" aria-label="Card back">
    <div class="brand-name">pexla</div>
  </section>
</body>
</html>
```